Moxy Fen needs some awesome stationary

Do you have what it takes to get my brand? You either do or you don't, have a crack at a design and you my just win my business.

I don't want to waste your or my time, so put your creative genius on either a business card or envelope.

I however need a package of stationary that follows the same brand. I will message you to complete the remaining should I like your first submission.

Here is what I need, have a go!

Basically I need the following for my small business based in melbourne.
- Letterhead (printer ready and MS Word)
- Business Card
- Compliments Slip
- Envelope
- Proposal Cover Page (MS Word only)
- Presentation Folder
- Marbled Fox Cards
- Student Name Tent
- Index Cards
- Vell-Ka

I am establishing the brand and it must be modern, professional but also relaxed; that is not formal and not corporate. It represents a company are leaders, but small enough to care and operate like a bunch of friends. We are bringing people and conversations back to business, and turfing out all the bureaucracy and crazy and wasteful procedures. Its about "lets talk and figure it out together and find even better ways".

Target Market(s)

Mainly companies that build software products, but Agile practices are used in many other industries (even graphic design projects)

Industry/Entity Type

Information Technology

Font styles to use
Sans Serif

Colors
3176b5
aaaaaa

Requirements
Must have
• I like curves and circles and not boxes or rectangles.
• I want a colour rich design with my brand colours, but it must be balanced.
• I want more modern than traditional, but simple modern
Should not have
• Not corporate
• Please don't waste my time if your not going to think about it.
• Don't mess with my primary logo
• Don't change my colours
• Don't overlay logo on image

```html
<!DOCTYPE html>
<html lang="en">
<head>
<meta charset="utf-8">
<title>Moxy Fen – Business Card</title>
<link rel="stylesheet" href="https://fonts.googleapis.com/css2?family=Open+Sans:wght@400;600;700&display=swap">
<style>
  :root {
    --brand-blue: #3176b5;
    --deep-blue: #1f4f9c;
    --card-blue: #2a5ba6;
    --brand-grey: #aaaaaa;
    --paper: #f1f1f1;
    --backdrop: #e4e4e4;
    --white: #ffffff;
  }
  * { margin: 0; padding: 0; box-sizing: border-box; }
  html, body {
    width: 1200px; height: 800px; overflow: hidden;
    background: var(--backdrop);
    font-family: "Open Sans", Arial, sans-serif;
  }
  .stage { position: relative; width: 1200px; height: 800px; }
  .card {
    position: absolute; top: 250px;
    width: 430px; height: 278px; overflow: hidden;
  }
  .card-front { left: 112px; background: var(--paper); }
  .card-back { left: 651px; background: radial-gradient(circle at 50% 45%, #3063ae 0%, var(--card-blue) 70%); }

  .paper-texture {
    position: absolute; inset: 0;
    background: radial-gradient(circle at 30% 50%, #f6f6f6 0%, #ebebeb 100%);
  }
  .blue-panel { position: absolute; inset: 0; }

  .brand-block {
    position: absolute; left: 0; width: 184px; top: 84px;
    display: flex; flex-direction: column; align-items: center;
  }
  .brand-dot {
    width: 54px; height: 54px; border-radius: 50%;
    background: var(--brand-blue); margin-bottom: 10px;
  }
  .brand-name {
    font-weight: 700; font-size: 27px; color: var(--deep-blue);
    letter-spacing: 0.2px; white-space: nowrap;
  }

  .contact {
    position: absolute; left: 229px; top: 62px; color: var(--white);
  }
  .person-name { font-size: 19px; font-weight: 400; line-height: 1.2; }
  .person-title { font-size: 9.5px; font-weight: 600; margin-top: 6px; white-space: nowrap; }
  .contact-list { list-style: none; margin-top: 22px; font-size: 12.5px; line-height: 18.5px; }
  .contact-list li { display: flex; align-items: flex-start; white-space: nowrap; }
  .contact-list svg { width: 11px; height: 11px; margin: 4px 10px 0 0; flex: none; fill: var(--white); }

  .back-brand {
    position: absolute; left: 0; right: 0; top: 94px;
    text-align: center; color: var(--white);
    font-weight: 700; font-size: 38px;
  }
  .back-url {
    position: absolute; left: 0; right: 0; top: 194px;
    text-align: center; color: var(--white); font-size: 15px; letter-spacing: 0.3px;
  }
</style>
</head>
<body>
<main class="stage">
  <section class="card card-front">
    <div class="paper-texture" role="img" aria-label="Fine concentric line pattern on light grey paper"></div>
    <svg class="blue-panel" viewBox="0 0 430 278" aria-hidden="true">
      <defs>
        <linearGradient id="panelShade" x1="0" y1="0" x2="1" y2="1">
          <stop offset="0" stop-color="#1d4c98"/>
          <stop offset="1" stop-color="#2a5ba6"/>
        </linearGradient>
      </defs>
      <path d="M200 0 H430 V278 H208 C 162 226, 154 62, 200 0 Z" fill="url(#panelShade)"/>
    </svg>

    <div class="brand-block">
      <span class="brand-dot"></span>
      <span class="brand-name">Moxy Fen</span>
    </div>

    <div class="contact">
      <h1 class="person-name">Dara Quillon</h1>
      <p class="person-title">CEO, Principal Agile Team Coach</p>
      <ul class="contact-list">
        <li>
          <svg viewBox="0 0 12 12"><path d="M6 0a4 4 0 0 0-4 4c0 3 4 8 4 8s4-5 4-8a4 4 0 0 0-4-4zm0 5.6A1.6 1.6 0 1 1 6 2.4a1.6 1.6 0 0 1 0 3.2z"/></svg>
          <span>PO Box 4417, Larkhill Vale,<br>VIC 3999, Australia</span>
        </li>
        <li>
          <svg viewBox="0 0 12 12"><path d="M0 2h12v8H0zM1 3v.4l5 3.4 5-3.4V3zm0 1.6V9h10V4.6L6 8z"/></svg>
          <span>dara@moxy-fen.com.au</span>
        </li>
        <li>
          <svg viewBox="0 0 12 12"><path d="M2.4 0.5l2 2.2-1 1.4c.8 1.7 2 2.9 3.6 3.7l1.4-1 2.2 2-1.2 2.2C5 10.6 1.4 7 0.5 1.6z"/></svg>
          <span>+61 400 000 123</span>
        </li>
      </ul>
    </div>
  </section>

  <section class="card card-back">
    <p class="back-brand">Moxy Fen</p>
    <p class="back-url">www.moxy-fen.com.au</p>
  </section>
</main>
</body>
</html>
```